Verdant Systems Business Card

want the back of card to be blue- with the logo in the center
front of card- info plus logo (info being mailing address, email address, and website address )
4 different names with titles to have on cards
1) Calvin Borsted - Owner
2) Naomi Trelvik- Customer Relationship Specialist
3) Felix Andrade- Vice President of Sales
4) Owen Markby- Chief Technology Officer

Target Market(s)

tech company in the government/probation office industry

Industry/Entity Type

Government Office

Contact Information for Business Card

1) Calvin Borsted - Owner

Colors
0355a3
ffffff

Requirements
Must have
• back side should be blue, with the logo placed in the center
• front side needs to include both the logo, as well as company info (info should include website address, email address, and mailing address)

```html
<!DOCTYPE html>
<html lang="en">
<head>
<meta charset="utf-8">
<title>Verdant Systems Business Card</title>
<link rel="stylesheet" href="https://fonts.googleapis.com/css2?family=Crimson+Pro:wght@500&family=Roboto:wght@400&display=swap">
<style>
  :root {
    --backdrop: #b3b0b0;
    --navy: #263661;
    --navy-text: #24325e;
    --paper: #fbfbfa;
    --grey-text: #6f6f78;
    --white: #ffffff;
  }
  html, body {
    margin: 0;
    padding: 0;
    width: 1200px;
    height: 1200px;
    overflow: hidden;
    background: var(--backdrop);
  }
  .canvas {
    position: relative;
    width: 1200px;
    height: 1200px;
  }
  .card {
    position: absolute;
    border-radius: 24px;
    box-sizing: border-box;
  }
  .card--back {
    left: 238px;
    top: 117px;
    width: 712px;
    height: 420px;
    background: var(--navy);
    display: flex;
    align-items: center;
    justify-content: center;
  }
  .card--front {
    left: 231px;
    top: 645px;
    width: 711px;
    height: 415px;
    background: var(--paper);
  }
  .brand-name {
    font-family: "Crimson Pro", Georgia, serif;
    font-weight: 500;
    margin: 0;
    white-space: nowrap;
    text-transform: uppercase;
  }
  .card--back .brand-name {
    color: var(--white);
    font-size: 72px;
    letter-spacing: 2px;
  }
  .person-name {
    position: absolute;
    left: 37px;
    top: 40px;
    margin: 0;
    font-family: "Crimson Pro", Georgia, serif;
    font-weight: 500;
    font-size: 27px;
    letter-spacing: 0.5px;
    color: var(--navy-text);
    text-transform: uppercase;
  }
  .person-title {
    position: absolute;
    left: 37px;
    top: 78px;
    margin: 0;
    font-family: "Roboto", Arial, sans-serif;
    font-size: 17px;
    color: var(--grey-text);
  }
  .address {
    position: absolute;
    left: 37px;
    top: 246px;
    margin: 0;
    font-family: "Roboto", Arial, sans-serif;
    font-style: normal;
    font-size: 17px;
    line-height: 29px;
    color: var(--grey-text);
  }
  .contact-list {
    position: absolute;
    left: 37px;
    top: 307px;
    margin: 0;
    padding: 0;
    list-style: none;
    font-family: "Roboto", Arial, sans-serif;
    font-size: 17px;
    color: var(--grey-text);
  }
  .contact-list li {
    display: flex;
    align-items: center;
    height: 26px;
  }
  .contact-list svg {
    width: 16px;
    height: 16px;
    margin-right: 14px;
    fill: var(--navy-text);
  }
  .front-brand {
    position: absolute;
    right: 36px;
    top: 320px;
  }
  .card--front .brand-name {
    color: var(--navy-text);
    font-size: 40px;
    letter-spacing: 1px;
  }
</style>
</head>
<body>
<main class="canvas">
  <section class="card card--back" aria-label="Card back">
    <p class="brand-name">Verdant Systems</p>
  </section>

  <section class="card card--front" aria-label="Card front">
    <h1 class="person-name">Naomi Trelvik</h1>
    <p class="person-title">Customer Relationship Specialist</p>

    <address class="address">418 Halden Ave., Brookmere,<br>Carrow Falls, US 604217</address>

    <ul class="contact-list">
      <li>
        <svg viewBox="0 0 16 16" aria-hidden="true"><path d="M2 6c0-2 3-3.5 6-3.5S14 4 14 6v1h-3V5.5H5V7H2zM3 8h10l1 5H2z"/></svg>
        555-274-3019
      </li>
      <li>
        <svg viewBox="0 0 16 16" aria-hidden="true"><path d="M1 3h14v10H1zM2 4.2v.4l6 4.2 6-4.2v-.4z" fill-rule="evenodd"/></svg>
        naomi.t@verdantsystems.com
      </li>
      <li>
        <svg viewBox="0 0 16 16" aria-hidden="true"><circle cx="8" cy="8" r="6.5" fill="none" stroke="#24325e" stroke-width="1.4"/><path d="M1.5 8h13M8 1.5c-3 3.5-3 9.5 0 13M8 1.5c3 3.5 3 9.5 0 13" fill="none" stroke="#24325e" stroke-width="1.2"/></svg>
        www.verdantsystems.com
      </li>
    </ul>

    <div class="front-brand">
      <p class="brand-name">Verdant Systems</p>
    </div>
  </section>
</main>
</body>
</html>
```